Half page (a5) ad for a company

I need a design for an ad for a company to be published in a conference catalogue. Please find enclosed the logo for a company. The company is providing health screening services. Ad should be subtle and minimalistic, i.e. logo in the centre and a phrase saying: "Be in charge of your own health" and the website bluefen.co.uk. Also please find enclosed guidlines for colours and fonts to be used.

```html
<!DOCTYPE html>
<html lang="en">
<head>
<meta charset="utf-8">
<title>The Blue Fen Private – A5 Advert</title>
<link href="https://fonts.googleapis.com/css2?family=Montserrat:wght@400;700&display=swap" rel="stylesheet">
<style>
  :root {
    --page-bg: #f3f2f2;
    --ink-black: #050606;
    --brand-red: #ed1c24;
    --text-white: #ffffff;
  }
  * { box-sizing: border-box; margin: 0; padding: 0; }
  html, body {
    width: 1200px;
    height: 1200px;
    overflow: hidden;
    background: var(--page-bg);
  }
  .canvas {
    position: relative;
    width: 1200px;
    height: 1200px;
  }
  .advert {
    position: absolute;
    left: 216px;
    top: 58px;
    width: 767px;
    height: 1077px;
    display: flex;
    flex-direction: column;
    font-family: "Montserrat", sans-serif;
  }
  .advert__brand-panel {
    position: relative;
    height: 726px;
    background: var(--ink-black);
  }
  .brand-mark {
    position: absolute;
    left: 0;
    right: 0;
    top: 250px;
    display: flex;
    flex-direction: column;
    align-items: center;
  }
  .brand-mark__dot {
    width: 120px;
    height: 120px;
    border-radius: 50%;
    background: var(--brand-red);
    margin-bottom: 150px;
  }
  .brand-mark__name {
    color: var(--brand-red);
    font-weight: 400;
    font-size: 72px;
    line-height: 1;
    letter-spacing: 0;
    text-align: center;
  }
  .brand-mark__name span { display: block; }
  .brand-mark__name span + span { margin-top: 18px; }
  .advert__message-panel {
    flex: 1;
    background: var(--brand-red);
    display: flex;
    flex-direction: column;
    align-items: center;
    padding-top: 104px;
  }
  .tagline {
    color: var(--text-white);
    font-weight: 700;
    font-size: 40px;
    line-height: 1.2;
    text-align: center;
  }
  .website {
    margin-top: 22px;
    color: var(--ink-black);
    font-weight: 400;
    font-size: 22px;
    letter-spacing: 0.5px;
  }
</style>
</head>
<body>
  <div class="canvas">
    <article class="advert">
      <section class="advert__brand-panel">
        <div class="brand-mark">
          <div class="brand-mark__dot"></div>
          <h1 class="brand-mark__name"><span>The Blue Fen</span><span>Private</span></h1>
        </div>
      </section>
      <section class="advert__message-panel">
        <p class="tagline">Be in charge of your own health</p>
        <p class="website">bluefen.co.uk</p>
      </section>
    </article>
  </div>
</body>
</html>
```